Web redesign for Windows software

We're a small & dynamic development team.
Our website www.vantrelo.com hosts a popular, free application virtualization software for Windows.
This technology was complex to develop, yet simple to use.
We've been a Freeware soft so far, and now we want to introduce a commercial, paying version.

We want to make www.vantrelo.com look professional, and adapted to the new commercial requirements.

We like the homepage design of www.pluvex.com

We need a redesign of the homepage and a sample interior page.

Target Market(s)

Computer geeks

Industry/Entity Type

Software

Requirements
Must have
• - Must keep the same colors as current vantrelo.com (black, gray, gray, white)
- DOWNLOAD button must be the #1 goal
- Video should have a high-importance place (video not ready yet, but will be in this style: http://lnkr.example/QmzRt)
- Homepage should have buttons/links to: Personal, Business, Developers
- Full navigation on the bottom (Products, Blog, Forum, About, Contact etc)
- Login, Language buttons
- Image slider (i.e similar to the one on pluvex.com) with 3 images: a. intro: 'try apps without risking your system', b. try Windows apps without installing them, c. put your apps in the cloud, d. share apps to your IT users
Nice to have
• A slight refresh of the logo is welcome (i.e light / metal effect)

```html
<!DOCTYPE html>
<html lang="en">
<head>
<meta charset="utf-8">
<title>Vantrelo – Application Virtualization</title>
<link href="https://fonts.googleapis.com/css2?family=Arimo:wght@400;700&family=Archivo:wght@700;800&display=swap" rel="stylesheet">
<style>
:root{
  --ink:#1b1b1b;
  --header:#141414;
  --hero:#202020;
  --band:#d6d6d6;
  --page:#f3f3f3;
  --orange:#f7a30b;
  --text:#555;
  --muted:#7a7a7a;
  --white:#fff;
  --link:#1f6fb5;
  --footer:#cfcfcf;
}
*{margin:0;padding:0;box-sizing:border-box}
html,body{width:1200px;height:1087px;overflow:hidden}
body{position:relative;background:var(--page);font-family:Arimo,Arial,sans-serif;color:var(--text)}
.abs{position:absolute}
.site-header{left:0;top:0;width:1200px;height:75px;background:var(--header)}
.brand{left:242px;top:22px;display:flex;align-items:center;gap:8px;color:var(--white);font-size:21px;letter-spacing:1px}
.brand-dot{width:26px;height:26px;border-radius:50%;background:var(--white)}
.languages{left:890px;top:5px;display:flex;gap:2px}
.languages span{width:12px;height:8px;display:block}
.main-nav{left:465px;top:17px;width:386px;height:38px;background:#1c1c1c;border:1px solid #333;border-radius:4px;display:flex;align-items:center;font-size:9.5px;font-weight:700;color:#ddd}
.main-nav a{color:inherit;text-decoration:none;height:100%;display:flex;align-items:center;justify-content:center;border-right:1px solid #2f2f2f}
.main-nav a:last-child{border-right:none}
.login{left:904px;top:24px;width:56px;height:23px;background:#111;border:1px solid #2c2c2c;border-radius:4px;color:#eee;font-size:8px;font-weight:700;display:flex;align-items:center;justify-content:center;gap:4px}
.hero{left:0;top:75px;width:1200px;height:232px;background:var(--hero)}
.band{left:0;top:307px;width:1200px;height:120px;background:linear-gradient(#cfcfcf,#e4e4e4)}
.hero-visual{left:240px;top:100px;width:382px;height:315px;background:linear-gradient(160deg,#dfe9f3,#f4f4f4 55%,#2a2a2a 88%);border-radius:4px}
.hero-title{left:636px;top:130px;font-family:Archivo,Arial,sans-serif;font-weight:800;font-size:25px;line-height:29px;color:var(--orange)}
.hero-copy{left:638px;top:191px;width:300px;font-size:8.8px;line-height:13.6px;color:#e6e6e6}
.slider-dots{left:898px;top:277px;display:flex;gap:7px}
.slider-dots span{width:8px;height:8px;border-radius:50%;background:#777}
.slider-dots span.on{background:var(--orange)}
.download{left:692px;top:338px;width:213px;height:52px;border-radius:26px;background:#2b2b2b;padding:5px}
.download-inner{width:100%;height:100%;border-radius:21px;background:linear-gradient(#ffb92c,#f39a00);position:relative}
.download-label{position:absolute;left:6px;top:4px;width:145px;height:34px;border-radius:17px;background:linear-gradient(#5a5a5a,#2d2d2d);color:var(--white);padding:6px 0 0 22px;font-weight:700}
.download-label small{display:block;font-size:8px;line-height:8px}
.download-label b{display:block;font-size:13px;line-height:14px}
.download svg{position:absolute;right:12px;top:10px}
h2.section{font-family:Archivo,Arial,sans-serif;font-weight:700;font-size:17px;color:var(--orange)}
.intro{left:240px;top:492px;width:722px;font-size:8.8px;line-height:13.6px}
.col-title{font-size:13px;color:#444;width:200px;text-align:center}
.shot{border:2px solid #cfcfcf;background:linear-gradient(#e9edf3,#fafafa)}
.video{left:615px;top:593px;width:345px;height:138px;border:1px solid #bbb;background:#d3d3d3}
.video-art{position:absolute;left:0;top:0;width:100%;height:117px;background:linear-gradient(#cfcfcf,#bdbdbd)}
.play{position:absolute;left:152px;top:37px;width:42px;height:30px;border-radius:6px;background:#222}
.controls{position:absolute;left:0;bottom:0;width:100%;height:20px;background:#1a1a1a;color:#ddd;font-size:6.5px}
.progress{position:absolute;left:0;top:0;width:100%;height:3px;background:#555}
.progress i{display:block;width:100px;height:3px;background:#d33}
.body-copy{left:238px;top:752px;width:724px;font-size:8.8px;line-height:13.6px}
.history{font-size:9.8px;color:#444;line-height:22.5px;list-style:none}
.vote{left:585px;top:995px;display:flex;align-items:center;gap:4px;font-size:9.8px;color:var(--link)}
.vote span{width:12px;height:12px;border-radius:2px}
.site-footer{left:0;top:1045px;width:1200px;height:42px;background:var(--footer);border-top:1px solid #bbb}
.footer-brand{left:240px;top:1060px;display:flex;align-items:center;gap:8px;font-size:9px;color:#444}
.footer-brand i{width:16px;height:16px;border-radius:50%;background:#333;display:block}
.social{left:862px;top:1062px;display:flex;gap:4px;font-size:8px;color:#3b5a98}
.social span{border:1px solid #aab;background:#eef;padding:2px 4px;border-radius:2px}
</style>
</head>
<body>
<header class="abs site-header"></header>
<div class="abs brand"><span class="brand-dot"></span>VANTRELO</div>
<div class="abs languages" aria-label="Languages">
  <span style="background:#3a55a0"></span><span style="background:#e8e8f4"></span><span style="background:#222"></span><span style="background:#e2a21c"></span><span style="background:#d62b1f"></span>
</div>
<nav class="abs main-nav">
  <a href="#" style="width:54px"><svg width="13" height="12" viewBox="0 0 13 12"><path d="M6.5 0 13 6h-2v6H8V8H5v4H2V6H0z" fill="#f7a30b"/></svg></a>
  <a href="#" style="width:82px">ABOUT</a>
  <a href="#" style="width:82px">PERSONAL</a>
  <a href="#" style="width:83px">BUSINESS</a>
  <a href="#" style="width:83px">DEVELOPERS</a>
</nav>
<div class="abs login">LOGIN <svg width="7" height="5" viewBox="0 0 7 5"><path d="M0 0l3.5 4L7 0" stroke="#f7a30b" stroke-width="1.5" fill="none"/></svg></div>

<section class="abs hero"></section>
<div class="abs band"></div>
<div class="abs hero-visual" role="img" aria-label="Application launcher windows floating among clouds above a dock bar"></div>
<h1 class="abs hero-title">PUT YOUR APPS<br>IN THE CLOUD</h1>
<p class="abs hero-copy">Lorem Ipsum is simply dummy text of the printing and typesetting industry. Lorem Ipsum has been the industry's standard dummy text ever since the 1500s, when an unknown printer took a galley of type and scrambled it to make a type specimen book.</p>
<div class="abs slider-dots"><span class="on"></span><span></span><span></span></div>
<a class="abs download" href="#">
  <div class="download-inner">
    <div class="download-label"><small>DOWNLOAD NOW</small><b>VERSION 2.0.834</b></div>
    <svg width="28" height="22" viewBox="0 0 28 22"><path d="M7 18a6 6 0 0 1 1-11 8 8 0 0 1 15 2 5 5 0 0 1-1 9z" fill="none" stroke="#c97800" stroke-width="2"/><path d="M14 9v8m-3-3 3 3 3-3" stroke="#c97800" stroke-width="2" fill="none"/></svg>
  </div>
</a>

<h2 class="abs section" style="left:240px;top:462px">APPLICATION VIRTUALIZATION</h2>
<p class="abs intro">A virtual app (or portable app) is a single .EXE file that holds an entire application, including files, DLLs and registry. Virtual apps can be copied &amp; moved around like regular files and launched from anywhere without installation: home, office, Skyvault, USB disk-on-key, laptop, network shares. With Vantrelo's app virtualization, you can take your apps and data with you, anywhere.</p>

<div class="abs col-title" style="left:312px;top:560px">Screenshots</div>
<div class="abs col-title" style="left:688px;top:560px">Videos</div>
<div class="abs shot" style="left:240px;top:593px;width:162px;height:61px" role="img" aria-label="Screenshot of the app library"></div>
<div class="abs shot" style="left:417px;top:593px;width:168px;height:61px" role="img" aria-label="Screenshot of the app icon grid"></div>
<div class="abs shot" style="left:240px;top:670px;width:162px;height:61px" role="img" aria-label="Screenshot of the capture options"></div>
<div class="abs shot" style="left:417px;top:670px;width:168px;height:61px" role="img" aria-label="Screenshot of the file explorer"></div>
<div class="abs video">
  <div class="video-art" role="img" aria-label="Explainer video frame showing a cartoon office scene"></div>
  <div class="play"><svg width="42" height="30" viewBox="0 0 42 30"><path d="M16 8l12 7-12 7z" fill="#fff"/></svg></div>
  <div class="controls">
    <div class="progress"><i></i></div>
    <svg class="abs" style="left:10px;top:7px" width="8" height="9" viewBox="0 0 8 9"><path d="M0 0l8 4.5L0 9z" fill="#ddd"/></svg>
    <span class="abs" style="left:52px;top:8px">0:16 / 1:01</span>
  </div>
</div>

<p class="abs body-copy">With Vantrelo's application virtualization, you can package an entire application - including all its files, DLLs, registry - into one single file and take it with you anywhere, along with the app's settings &amp; data. On your Skyvault drive, on a USB stick, at work, at home, on your laptop - using application virtualization you will no longer have to reinstall your apps again and again everytime you move from one computer to another. Virtual portable apps also keep your computer stable, isolating apps from your system. Whether your are a home user or an IT administrator, Vantrelo will save you precious time... and frustration.</p>

<h2 class="abs section" style="left:240px;top:840px">VERSION HISTORY</h2>
<ul class="abs history" style="left:255px;top:866px">
  <li>24 Oct 2012: Build 2.0.834: fixed UI Settings menu crash</li>
  <li>25 Jun 2012: Build 2.0.831: fixed rare UI crash on startup</li>
  <li>07 Mar 2012: Translated into 3 languages</li>
  <li>22 Sep 2011: Integration with Skyvault cloud drive</li>
  <li>06 Mar 2011: Version 1.6 released</li>
  <li>28 Sep 2010: Version 1.5 released</li>
</ul>
<ul class="abs history" style="left:590px;top:866px">
  <li>30 Jul 2012: Build 2.0.832: downloads directory made portable</li>
  <li>14 Jun 2012: Version 2.0 is released</li>
  <li>30 Jan 2012: Beta 2.0 available for download</li>
  <li>13 Jul 2011: Version 1.7 released</li>
  <li>15 Nov 2011: Version 1.55 released</li>
</ul>
<div class="abs vote"><span style="background:#f08a24"></span><span style="background:#3b5a98"></span>&nbsp;Vote for features</div>

<footer class="abs site-footer"></footer>
<div class="abs footer-brand"><i></i>Vantrelo © 2011 Privacy Policy</div>
<div class="abs social"><span>Like</span><span style="color:#333">470</span><span>Send</span></div>
</body>
</html>
```